Simple Logo Design for Semi-Clear Plastic Frosted Card stock

Create a business card on frosted plastic. compliment existing logo elements with a tree trunk, roots, or seed at the lower half and the full logo both on the front.

Contact information will go on a solid portion of the back of this design since this card stock is semi-transparent.

It is important to consider this plastic card stock medium in your design. I found helpful tips and guides listed at vellaprint-sample.net: be careful to understand ink printed on plastic cards cannot have too much of a consistent print area or risks peeling and fine lines can easily scratch off.
Updates

2" x 3.5" 20PT Clear Plastic Business cards with Round corners Please get info or templates here: https://www.vellaprint-sample.net/product-detail/2-x-35-20pt-clear-plastic-business-cards-with-round-corners

Target Market(s)

Not for profit- religion

Industry/Entity Type

Business

Must include complementary elements to the existing logo

Font styles to use
Decorative

Colors
000000

Requirements
Must have
• Elements of community, nature and oneness. Such as: seed, roots, tree trunk, etc.
• Three lines of space on the back for Name, Title, Phone Number.
Nice to have
• I like a light use of decorative elements
Should not have
• No eyes, from faces or animals.

```html
<!DOCTYPE html>
<html lang="en">
<head>
<meta charset="utf-8">
<title>Steadfast Grove – Business Card</title>
<link href="https://fonts.googleapis.com/css2?family=Jost:wght@400&family=Source+Sans+3:wght@400;600&display=swap" rel="stylesheet">
<style>
  :root {
    --stage: #000000;
    --card: #303033;
    --teal: #2f8480;
    --green: #3d9a46;
    --muted: #a9aaad;
    --white: #ffffff;
  }
  * { margin: 0; padding: 0; box-sizing: border-box; }
  html, body { width: 1200px; height: 900px; overflow: hidden; background: var(--stage); }
  .canvas { position: relative; width: 1200px; height: 900px; }

  .card {
    position: absolute;
    top: 271px;
    width: 457px;
    height: 281px;
    background: var(--card);
    border-radius: 14px;
    overflow: hidden;
  }
  .card--back { left: 137px; }
  .card--front { left: 626px; }

  .brand {
    position: absolute;
    left: 0; right: 0;
    text-align: center;
  }
  .brand__mark {
    display: block;
    margin: 0 auto 12px;
    width: 46px; height: 46px;
    border-radius: 50%;
    background: var(--teal);
  }
  .brand__name {
    font-family: "Jost", sans-serif;
    font-weight: 400;
    font-size: 28px;
    line-height: 30px;
    letter-spacing: 1px;
    color: var(--teal);
    text-transform: uppercase;
  }
  .brand__tagline {
    font-family: "Jost", sans-serif;
    font-weight: 400;
    font-size: 11px;
    line-height: 14px;
    letter-spacing: 1px;
    color: var(--muted);
    text-transform: uppercase;
    margin-top: -2px;
  }
  .card--back .brand { top: 67px; }
  .card--front .brand { top: 108px; }

  .divider {
    position: absolute;
    top: 203px;
    height: 1px;
    background: var(--green);
  }
  .divider--left { left: 0; width: 157px; }
  .divider--right { right: 0; width: 155px; }

  .contact {
    position: absolute;
    left: 0; right: 0;
    top: 192px;
    text-align: center;
    font-family: "Source Sans 3", sans-serif;
  }
  .contact__name {
    font-size: 17px;
    font-weight: 600;
    line-height: 22px;
    color: var(--teal);
  }
  .contact__surname { color: var(--green); }
  .contact__title {
    font-size: 13px;
    line-height: 15px;
    color: var(--white);
  }
  .contact__phone {
    margin-top: 12px;
    font-size: 13px;
    color: var(--white);
    display: inline-flex;
    align-items: center;
    gap: 4px;
  }
  .contact__phone svg { width: 10px; height: 10px; }
</style>
</head>
<body>
<main class="canvas">

  <section class="card card--back">
    <div class="brand">
      <span class="brand__mark"></span>
      <div class="brand__name">Steadfast Grove</div>
      <div class="brand__tagline">Learning, Kinship &amp; Harmony</div>
    </div>
    <span class="divider divider--left"></span>
    <span class="divider divider--right"></span>
    <div class="contact">
      <div class="contact__name">Daniel <span class="contact__surname">Marsh</span></div>
      <div class="contact__title">Managing Director</div>
      <div class="contact__phone">
        <svg viewBox="0 0 24 24" aria-hidden="true"><path fill="#3d9a46" d="M6.6 10.8a15.1 15.1 0 0 0 6.6 6.6l2.2-2.2a1 1 0 0 1 1-.25 11.4 11.4 0 0 0 3.6.57 1 1 0 0 1 1 1V20a1 1 0 0 1-1 1A17 17 0 0 1 3 4a1 1 0 0 1 1-1h3.5a1 1 0 0 1 1 1c0 1.25.2 2.45.57 3.570a1 1 0 0 1-.25 1z"/></svg>
        (044)-555-0142
      </div>
    </div>
  </section>

  <section class="card card--front">
    <div class="brand">
      <span class="brand__mark"></span>
      <div class="brand__name">Steadfast Grove</div>
      <div class="brand__tagline">Learning, Kinship &amp; Harmony</div>
    </div>
  </section>

</main>
</body>
</html>
```